Business Card Design For Office Furniture Clearance Company

Kestrel Office Clearance - our company name pretty much explains what we do, we clear offices for high end clients, mainly plc's and large international companies.

We require a nice looking business card that displays professionalism but without being too serious.

It would be nice to see just a little more than a conventional boring business card, make sure you add some flare.

Industry/Entity Type

Office Furniture

Contact Information for Business Card

CARD 1

Mark Holloway
Director
mark@kestrelofficeclearance.co.uk
m: 07700 153928

t: 01632 960418
www.kestrelofficeclearance.co.uk

Kestrel Office Clearance
Unit K4 B
2-8 Fenwick Lane
Ashcombe
Hartfield
ZZ9 4QT

free office clearances… you cant get better than that.

CARD 2

Peter Radford
Director
peter@kestrelofficeclearance.co.uk
m: 07700 382615

t: 01632 960418

Kestrel Office Clearance
Unit K4 B
2-8 Fenwick Lane
Ashcombe
Hartfield
ZZ9 4QT

Font styles to use
Sans Serif

Requirements
Must have
• A white background - as we have a blue logo.
Nice to have
• Nice use of the logo - play around with this and dissect it.

```html
<!DOCTYPE html>
<html lang="en">
<head>
<meta charset="utf-8">
<title>Kestrel Office Clearance – Business Card</title>
<link href="https://fonts.googleapis.com/css2?family=Source+Sans+3:ital,wght@0,400;0,600;1,400&display=swap" rel="stylesheet">
<style>
  :root {
    --brand-blue: #0a66a6;
    --ink: #4a4a4a;
    --rule: #3c3c3c;
    --card-white: #fbfbfb;
    --backdrop: #e4e4e4;
    --disc-light: #eef0f3;
  }
  * { margin: 0; padding: 0; box-sizing: border-box; }
  html, body {
    width: 1105px; height: 1200px; overflow: hidden;
    background: var(--backdrop);
    font-family: "Source Sans 3", "Myriad Pro", Arial, sans-serif;
  }
  .canvas { position: relative; width: 1105px; height: 1200px; }
  .card {
    position: absolute; left: 182px; width: 747px; height: 427px;
  }
  .card-front { top: 119px; background: var(--card-white); }
  .card-back { top: 637px; background: var(--brand-blue); }

  .brand-disc { position: absolute; border-radius: 50%; }
  .card-front .brand-disc {
    left: 526px; top: 33px; width: 182px; height: 182px; background: var(--brand-blue);
  }
  .brand-name {
    position: absolute; white-space: nowrap; font-weight: 600; text-align: right;
  }
  .card-front .brand-name {
    right: 238px; top: 107px; font-size: 26px; color: var(--brand-blue);
  }

  .person-name {
    position: absolute; left: 35px; top: 212px;
    font-size: 27px; font-weight: 600; color: var(--brand-blue);
  }
  .person-role {
    position: absolute; left: 35px; top: 242px;
    font-size: 19px; color: var(--rule);
  }
  .role-rule {
    position: absolute; left: 114px; top: 265px; width: 596px; height: 2px; background: var(--rule);
  }

  .contact-list { position: absolute; left: 35px; top: 284px; list-style: none; }
  .contact-list li {
    display: flex; align-items: center; height: 29px;
    font-size: 19px; color: var(--ink);
  }
  .contact-list svg { width: 18px; height: 18px; margin-right: 11px; fill: var(--brand-blue); flex: none; }

  .company-address {
    position: absolute; right: 37px; top: 314px; text-align: right;
    font-style: normal; font-size: 19px; line-height: 27px; color: var(--ink);
  }
  .company-address .company-name { color: var(--brand-blue); font-weight: 600; }

  .tagline {
    position: absolute; left: 56px; top: 320px;
    font-size: 19px; font-style: italic; line-height: 26px; color: #fff;
  }
  .card-back .brand-disc {
    left: 569px; top: 255px; width: 144px; height: 144px; background: var(--disc-light);
  }
  .card-back .brand-name {
    right: 196px; top: 315px; font-size: 20px; color: #fff;
  }
</style>
</head>
<body>
<main class="canvas">
  <section class="card card-front" aria-label="Business card front">
    <span class="brand-name">Kestrel Office Clearance</span>
    <span class="brand-disc"></span>

    <h1 class="person-name">Mark Holloway</h1>
    <p class="person-role">Director</p>
    <span class="role-rule"></span>

    <ul class="contact-list">
      <li>
        <svg viewBox="0 0 24 24" aria-hidden="true"><path d="M6.6 10.8a15.1 15.1 0 0 0 6.6 6.6l2.2-2.2a1 1 0 0 1 1-.25 11.4 11.4 0 0 0 3.6.57 1 1 0 0 1 1 1V20a1 1 0 0 1-1 1A17 17 0 0 1 3 4a1 1 0 0 1 1-1h3.5a1 1 0 0 1 1 1c0 1.25.2 2.45.57 3.57a1 1 0 0 1-.25 1z"/></svg>
        01632 960418
      </li>
      <li>
        <svg viewBox="0 0 24 24" aria-hidden="true"><path d="M7 1h10a2 2 0 0 1 2 2v18a2 2 0 0 1-2 2H7a2 2 0 0 1-2-2V3a2 2 0 0 1 2-2zm0 3v14h10V4zm5 15.2a1.1 1.1 0 1 0 0 2.2 1.1 1.1 0 0 0 0-2.2z"/></svg>
        07700 153928
      </li>
      <li>
        <svg viewBox="0 0 24 24" aria-hidden="true"><path d="M2 5h20v14H2zm2 2v.4l8 5.2 8-5.2V7zm0 2.8V17h16V9.8l-8 5.2z"/></svg>
        mark@kestrelofficeclearance.co.uk
      </li>
      <li>
        <svg viewBox="0 0 24 24" aria-hidden="true"><path d="M12 2a10 10 0 1 0 0 20 10 10 0 0 0 0-20zm-1 17.9A8 8 0 0 1 4.1 11H7v2l4 4zm6.9-2.5A2 2 0 0 0 16 16h-1v-3a1 1 0 0 0-1-1H8v-2h2a1 1 0 0 0 1-1V7h2a2 2 0 0 0 2-2v-.4a8 8 0 0 1 2.9 12.8z"/></svg>
        www.kestrelofficeclearance.co.uk
      </li>
    </ul>

    <address class="company-address">
      <span class="company-name">Kestrel Office Clearance</span><br>
      Unit K4 B, 2-8 Fenwick Lane<br>
      Ashcombe, Hartfield, ZZ9 4QT
    </address>
  </section>

  <section class="card card-back" aria-label="Business card back">
    <p class="tagline">Free office clearances…<br>you cant get better than that.</p>
    <span class="brand-name">Kestrel Office Clearance</span>
    <span class="brand-disc"></span>
  </section>
</main>
</body>
</html>
```